Anzeigengestaltung für Reinigungsunternehmen
Zielgruppe
Wir sind ein Reinigungsunternehmen mit den Haupttätigkeitsfeldern: Büroreinigung, Treppenhausreinigung und Bauendreinigung.
Webseite: www.kolbrapflege.de
Die Zielgruppe sind Unternehmer (überwiegend Büros), Hausverwaltungen sowie Bauherren.
Aufgabenstellung
Die Reinigungsfirma wird mit dieser Anzeige zum ersten Mal beworben.
Umkreis: Kreis Paderborn und Kreis Gütersloh
Die Anzeige soll sowohl in Facebook beworben werden, sowie auch in den örtlichen Rundschauen.

```html
<!DOCTYPE html>
<html lang="de">
<head>
<meta charset="utf-8">
<title>Kolbra Pflege – Anzeige</title>
<link href="https://fonts.googleapis.com/css2?family=Montserrat:ital,wght@0,400;0,500;0,700;1,400&display=swap" rel="stylesheet">
<style>
  :root {
    --brand-blue: #1a40e2;
    --brand-teal: #40bfb1;
    --text-navy: #1d4a7a;
    --white: #ffffff;
    --photo-light: #e9edf1;
    --photo-mid: #c9d2dc;
    --photo-dark: #8e9cb0;
  }
  * { margin: 0; padding: 0; box-sizing: border-box; }
  html, body { width: 1200px; height: 740px; overflow: hidden; background: var(--white); }
  body { font-family: "Montserrat", Arial, sans-serif; }
  .ad {
    position: relative;
    width: 1200px;
    height: 740px;
    overflow: hidden;
    background: var(--white);
  }
  .photo-area {
    position: absolute;
    inset: 0;
    width: 1200px;
    height: 740px;
  }
  .headline-band {
    position: absolute;
    inset: 0;
    width: 1200px;
    height: 740px;
  }
  .headline {
    position: absolute;
    left: 66px;
    top: 112px;
    color: var(--white);
    font-weight: 700;
    font-size: 46px;
    line-height: 62px;
    letter-spacing: 0.2px;
  }
  .brand {
    position: absolute;
    left: 690px;
    top: 128px;
    display: flex;
    align-items: center;
    gap: 16px;
    color: var(--white);
  }
  .brand-mark {
    width: 46px;
    height: 46px;
    background: var(--white);
  }
  .brand-name {
    font-weight: 700;
    font-size: 34px;
    line-height: 38px;
  }
  .brand-owner {
    font-weight: 700;
    font-size: 13px;
    line-height: 18px;
    margin-top: 6px;
  }
  .tagline {
    position: absolute;
    left: 66px;
    top: 312px;
    color: var(--white);
    font-style: italic;
    font-weight: 400;
    font-size: 29px;
    line-height: 44px;
  }
  .services {
    position: absolute;
    left: 80px;
    top: 476px;
    list-style: none;
    color: var(--text-navy);
    font-size: 34px;
    font-weight: 400;
    letter-spacing: 0.4px;
  }
  .services li {
    display: flex;
    align-items: center;
    gap: 14px;
    height: 64px;
  }
  .service-icon { width: 40px; height: 36px; flex: none; }
</style>
</head>
<body>
<div class="ad">
  <svg class="photo-area" viewBox="0 0 1200 740" role="img" aria-label="Foto: Reinigungskraft mit gelben Handschuhen, blauem Eimer und Wischmopp in einem hellen Büro">
    <defs>
      <linearGradient id="photoTone" x1="0" y1="0" x2="1" y2="1">
        <stop offset="0" stop-color="var(--photo-light)"/>
        <stop offset="0.6" stop-color="var(--photo-mid)"/>
        <stop offset="1" stop-color="var(--photo-dark)"/>
      </linearGradient>
    </defs>
    <polygon points="756,0 1200,0 1200,740 590,740" fill="url(#photoTone)"/>
  </svg>

  <svg class="headline-band" viewBox="0 0 1200 740" aria-hidden="true">
    <polygon points="0,62 1046,62 976,276 0,276" fill="var(--brand-blue)"/>
    <polygon points="0,286 973,286 936,414 0,414" fill="var(--brand-teal)"/>
  </svg>

  <h1 class="headline">Schenken Sie Ihrem<br>Objekt neuen Glanz!</h1>

  <div class="brand">
    <div class="brand-mark"></div>
    <div>
      <div class="brand-name">Kolbra Pflege</div>
      <div class="brand-owner">Inh. Marco Lindqvist</div>
    </div>
  </div>

  <p class="tagline">Zuverlässig und professionelle<br>Reinigungskräfte in Paderborn &amp; Gütersloh</p>

  <ul class="services">
    <li>
      <svg class="service-icon" viewBox="0 0 40 36" aria-hidden="true">
        <line x1="22" y1="16" x2="37" y2="4" stroke="var(--text-navy)" stroke-width="3" stroke-linecap="round"/>
        <path d="M3 30 C6 20 14 13 22 15 C25 22 17 30 3 30 Z" fill="var(--text-navy)"/>
      </svg>
      Büroreinigung
    </li>
    <li>
      <svg class="service-icon" viewBox="0 0 40 36" aria-hidden="true">
        <line x1="22" y1="16" x2="37" y2="4" stroke="var(--text-navy)" stroke-width="3" stroke-linecap="round"/>
        <path d="M3 30 C6 20 14 13 22 15 C25 22 17 30 3 30 Z" fill="var(--text-navy)"/>
      </svg>
      Treppenhausreinigung
    </li>
    <li>
      <svg class="service-icon" viewBox="0 0 40 36" aria-hidden="true">
        <line x1="22" y1="16" x2="37" y2="4" stroke="var(--text-navy)" stroke-width="3" stroke-linecap="round"/>
        <path d="M3 30 C6 20 14 13 22 15 C25 22 17 30 3 30 Z" fill="var(--text-navy)"/>
      </svg>
      Bauendreinigung
    </li>
  </ul>
</div>
</body>
</html>
```